Federal Government Proposal Development Consulting company needs a website designed and coded

I am looking for someone to design (using an existing logo, color palette, and text fonts) and code a wordpress-based website for a Proposal Development consulting company. I have full copy for all site pages and suggestions for images/ graphics and a few example design templates to go from.

One note, from a color perspective - I included a mockup of a business card to highlight a color scheme that I tend to like - if you look at the back of the business card, the blend of the grey, blue, with the neon green highlight as a separator really seems to pop. Just a thought as you are designing the page.

I would like to see 2-3 potential design layouts, and I will select one to move forward with. Then, I would like the site to be coded for WordPress (I can provide a login to my wordpress site). I would like 1 opportunity to review the coded site and make any final tweaks.

```html
<!DOCTYPE html>
<html lang="en">
<head>
<meta charset="UTF-8">
<title>The Quill Draft – Proposal Consulting</title>
<link href="https://fonts.googleapis.com/css2?family=Kurale&family=Poppins:wght@400;500;600&display=swap" rel="stylesheet">
<style>
:root{
  --navy:#0b0f4a;
  --navy-deep:#070a3a;
  --blue:#0a46c4;
  --blue-mid:#1b3fb0;
  --neon:#2ee6c8;
  --ink:#1d1f2e;
  --text:#3a3d4d;
  --muted:#8a8c98;
  --line:#d9dbe3;
  --paper:#f3f4f7;
  --white:#ffffff;
}
*{box-sizing:border-box;margin:0;padding:0}
html,body{width:1200px;height:5348px;overflow:hidden}
body{position:relative;background:var(--white);font-family:'Poppins',sans-serif;color:var(--text)}
.serif{font-family:'Kurale',serif}
.abs{position:absolute}

/* header */
.site-header{position:absolute;left:0;top:0;width:1200px;height:94px;background:var(--white)}
.brand{position:absolute;left:112px;top:24px;font-family:'Kurale',serif;color:var(--muted);font-size:36px;line-height:1}
.brand small{display:block;font-size:15px;margin-top:2px;padding-left:44px}
.nav{position:absolute;top:45px;left:0;font-size:15px;color:#555}
.nav a{position:absolute;white-space:nowrap;color:#555;text-decoration:none}
.nav .active{color:var(--navy);font-weight:500}
.nav .active::after{content:"";position:absolute;left:0;right:0;top:26px;height:3px;border-radius:2px;background:var(--neon)}

/* hero */
.hero{position:absolute;left:0;top:94px;width:1200px;height:514px;background:linear-gradient(90deg,var(--navy-deep) 0%,#14207a 45%,#6d7c93 70%,#c9ced6 100%)}
.hero h1{position:absolute;left:100px;top:118px;font-family:'Kurale',serif;font-weight:400;font-size:38px;color:var(--white)}
.hero p{position:absolute;left:100px;top:184px;width:440px;font-family:'Kurale',serif;font-size:22px;line-height:43px;color:var(--white)}
.notch{position:absolute;left:545px;top:566px;width:110px;height:110px;border-radius:50%;background:var(--white)}

.btn{position:absolute;display:flex;align-items:center;justify-content:center;gap:12px;border-radius:30px;font-family:'Kurale',serif;font-size:22px;text-decoration:none}
.btn-light{background:var(--white);color:var(--navy)}
.btn-dark{background:var(--navy);color:var(--white)}

.section-title{position:absolute;left:0;width:1200px;text-align:center;font-family:'Kurale',serif;font-weight:400;font-size:36px;color:var(--ink)}

/* what we do */
.intro{position:absolute;left:132px;width:936px;text-align:center;font-size:15.5px;line-height:33.5px;color:var(--text)}
.card{position:absolute;top:1225px;width:318px;height:478px;background:var(--white);border:1px solid #e3e4ea;border-radius:6px;box-shadow:0 4px 14px rgba(0,0,0,.08)}
.card-icon{position:absolute;left:27px;top:-45px;width:90px;height:90px;border-radius:50%;background:var(--white);border:1px solid #e3e4ea;display:flex;align-items:center;justify-content:center;box-shadow:0 2px 8px rgba(0,0,0,.07)}
.card h3{position:absolute;left:31px;top:72px;font-family:'Kurale',serif;font-weight:400;font-size:26px;color:var(--ink);white-space:nowrap}
.card p{position:absolute;left:31px;top:128px;width:265px;font-size:15px;line-height:33.5px;height:201px;overflow:hidden}

/* who we are */
.who{position:absolute;left:0;top:1796px;width:1200px;height:570px;background:linear-gradient(90deg,var(--navy-deep),#0d2a9c 70%,#0b3fc4)}
.who-rule{position:absolute;left:0;top:2366px;width:1200px;height:7px;background:var(--neon)}
.who h2{position:absolute;left:114px;top:62px;font-family:'Kurale',serif;font-weight:400;font-size:36px;color:var(--white)}
.who p{position:absolute;left:114px;top:142px;width:540px;font-size:15.5px;line-height:33.5px;color:var(--white)}
.photo{position:absolute;border-radius:3px}

/* services */
.services{position:absolute;left:0;top:2373px;width:1200px;height:783px;background:linear-gradient(135deg,#fafbfc,#eceef2 60%,#f6f7f9)}
.tile{position:absolute;width:257px;height:162px;background:var(--white);border-radius:4px;box-shadow:0 3px 12px rgba(0,0,0,.1);text-align:center}
.tile svg{position:absolute;left:93px;top:22px}
.tile span{position:absolute;left:0;right:0;top:108px;font-family:'Kurale',serif;font-size:22px;color:var(--ink)}
.tile.featured{background:linear-gradient(135deg,var(--navy),var(--blue))}
.tile.featured span{color:var(--white)}

/* expertise */
.expertise{position:absolute;left:0;top:3156px;width:1200px;height:315px;background:linear-gradient(90deg,#0a3fb8,var(--blue))}
.expertise h2{position:absolute;left:108px;top:70px;font-family:'Kurale',serif;font-weight:400;font-size:36px;color:var(--white)}
.arrow-btn{position:absolute;top:3231px;width:40px;height:40px;border:2px solid var(--white);border-radius:50%}
.ex-card{position:absolute;top:3328px;width:320px;height:342px;background:var(--white);border-radius:4px;box-shadow:0 4px 14px rgba(0,0,0,.12)}
.ex-card .photo{left:6px;top:6px;width:308px;height:258px}
.ex-card span{position:absolute;left:0;right:0;top:286px;text-align:center;font-family:'Kurale',serif;font-size:24px;color:var(--ink)}

/* contact */
.contact{position:absolute;left:0;top:3762px;width:1200px;height:577px;background:var(--paper)}
.field{position:absolute;height:57px;border:1px solid #c9cbd4;background:var(--white);font-size:14px;color:#555;padding:18px 16px}

/* testimonials */
.quote-card{position:absolute;top:4546px;width:564px;height:243px;border:1px solid #bfc2cc;border-radius:4px;background:var(--white);text-align:center}
.quote-card p{position:absolute;left:24px;right:24px;top:50px;font-size:15.5px;line-height:30px;font-style:italic;color:var(--text)}
.quote-card cite{position:absolute;left:0;right:0;top:180px;font-family:'Kurale',serif;font-style:normal;font-size:20px;color:var(--ink)}
.quote-card.faded{opacity:.45}
.qmark{position:absolute;top:-8px;font-family:'Kurale',serif;font-size:80px;line-height:1;color:var(--navy)}
.dot{position:absolute;top:4833px;width:34px;height:5px;border-radius:3px;background:#c9cbd4}

/* footer */
.site-footer{position:absolute;left:0;top:4933px;width:1200px;height:415px;background:var(--navy-deep);color:var(--white)}
.site-footer h4{position:absolute;top:60px;font-family:'Kurale',serif;font-weight:400;font-size:24px}
.flinks{position:absolute;left:519px;top:120px;font-size:15px;line-height:39.5px}
.flinks a{display:block;color:var(--white);text-decoration:none}
.fcontact{position:absolute;left:837px;font-size:15px}
.copyright{position:absolute;left:0;right:0;top:374px;text-align:center;font-size:13px}
</style>
</head>
<body>

<header class="site-header">
  <div class="brand">The Quill Draft<small>Consulting LLC</small></div>
  <nav class="nav">
    <a class="active" style="left:465px">Home</a>
    <a style="left:569px">Work with Us</a>
    <a style="left:729px">Work for Us</a>
    <a style="left:878px">About Us</a>
    <a style="left:1009px">Contact</a>
  </nav>
</header>

<section class="hero">
  <div class="photo" role="img" aria-label="Man with glasses working at a computer in a modern office" style="left:520px;top:0;width:680px;height:514px;background:linear-gradient(90deg,rgba(20,32,122,0),rgba(160,170,185,.5));border-radius:0"></div>
  <h1>Generate Success</h1>
  <p>Fuel Innovation in Proposal Excellence with The Quill Draft! Click here to explore our services.</p>
  <a class="btn btn-light" style="left:100px;top:350px;width:205px;height:56px">Get Started
    <svg width="26" height="14" viewBox="0 0 26 14"><path d="M1 7h23M18 1l6 6-6 6" fill="none" stroke="currentColor" stroke-width="2"/></svg></a>
</section>
<div class="notch"></div>
<svg class="abs" style="left:590px;top:584px" width="20" height="12" viewBox="0 0 20 12"><path d="M2 2l8 8 8-8" fill="none" stroke="#0b0f4a" stroke-width="2.5"/></svg>

<h2 class="section-title" style="top:710px">What We Do</h2>
<p class="intro" style="top:786px">The Quill Draft, specializes in advancing an organization through a comprehensive suite of services designed to modernize the proposal development process. From innovative Capture Management strategies that pinpoint lucrative opportunities, meticulous Proposal Development services that transform concepts into effective narratives, and cutting-edge Generative AI techniques that create domain-aware content accelerating proposal draft development, we are your dedicated partner in securing success. With a unique fusion of technical expertise and exceptional writing capabilities, we surpass industry standards and set new benchmarks for excellence.</p>
<p class="intro" style="top:1036px">Discover a dynamic approach to proposal consulting that goes beyond conventional boundaries—choose The Quill Draft for solutions that Enhance the quality of your work, Elevate your corporate advantage, and Expand your industry presence.</p>

<article class="card" style="left:108px">
  <div class="card-icon"><svg width="48" height="48" viewBox="0 0 48 48" fill="none" stroke="#0b0f4a" stroke-width="2"><circle cx="24" cy="24" r="16"/><circle cx="24" cy="24" r="9"/><circle cx="24" cy="24" r="3"/><path d="M24 2v8M24 38v8M2 24h8M38 24h8"/></svg></div>
  <h3>Capture Management</h3>
  <p>Elevate your business development strategy with our Capture Management services. From opportunity identification to strategic planning, our experts will guide you through a meticulous process, ensuring</p>
  <a class="btn btn-dark" style="left:31px;top:388px;width:199px;height:54px">Read More <svg width="26" height="14" viewBox="0 0 26 14"><path d="M1 7h23M18 1l6 6-6 6" fill="none" stroke="currentColor" stroke-width="2"/></svg></a>
</article>
<article class="card" style="left:440px">
  <div class="card-icon"><svg width="48" height="48" viewBox="0 0 48 48" fill="none" stroke="#0b0f4a" stroke-width="2"><path d="M6 42h36M10 42V30h6v12M20 42V24h6v18M30 42V18h6v24M8 24l12-10 8 6 14-12M36 8h6v6"/></svg></div>
  <h3>Proposal Development</h3>
  <p>Transform your vision into winning proposals with our Proposal Development services. We specialize in persuasive narratives, clear technical solutions, and strategic pricing models. From meticulous</p>
  <a class="btn btn-dark" style="left:31px;top:388px;width:199px;height:54px">Read More <svg width="26" height="14" viewBox="0 0 26 14"><path d="M1 7h23M18 1l6 6-6 6" fill="none" stroke="currentColor" stroke-width="2"/></svg></a>
</article>
<article class="card" style="left:770px">
  <div class="card-icon"><svg width="48" height="48" viewBox="0 0 48 48" fill="none" stroke="#0b0f4a" stroke-width="2"><circle cx="24" cy="24" r="14"/><circle cx="24" cy="24" r="20" stroke-dasharray="4 3"/><path d="M18 28l4-10 4 10M19.5 24h5M30 18v10"/></svg></div>
  <h3>Generative AI</h3>
  <p>Revolutionize your proposal writing process with our domain-aware Generative AI services. Using customer-installed tools, we leverage domain-aware artificial intelligence to</p>
  <a class="btn btn-dark" style="left:31px;top:388px;width:199px;height:54px">Read More <svg width="26" height="14" viewBox="0 0 26 14"><path d="M1 7h23M18 1l6 6-6 6" fill="none" stroke="currentColor" stroke-width="2"/></svg></a>
</article>

<section class="who">
  <h2>Who We Are</h2>
  <p>Sed ut perspiciatis unde omnis iste natus error sit voluptatem accusantium doloremque laudantium, totam rem aperiam, eaque ipsa quae ab illo inventore veritatis et quasi architecto beatae vitae dicta sunt explicabo. Nemo enim ipsam voluptatem quia voluptas sit aspernatur aut odit aut fugit, sed quia consequuntur magni dolores eos qui ratione voluptatem sequi nesciunt. Neque porro quisquam est, qui dolorem ipsum quia dolor sit amet, consectetur</p>
  <a class="btn btn-light" style="left:114px;top:452px;width:204px;height:58px">Read More <svg width="26" height="14" viewBox="0 0 26 14"><path d="M1 7h23M18 1l6 6-6 6" fill="none" stroke="currentColor" stroke-width="2"/></svg></a>
  <div class="photo" role="img" aria-label="Two colleagues reviewing a tablet in a server room" style="left:675px;top:45px;width:413px;height:478px;background:linear-gradient(160deg,#2a4f9e,#14307a 55%,#7d93b8)"></div>
</section>
<div class="who-rule"></div>

<section class="services">
  <h2 class="section-title" style="top:108px">Our Services</h2>
  <div class="tile featured" style="left:181px;top:201px"><svg width="70" height="70" viewBox="0 0 70 70" fill="none" stroke="#fff" stroke-width="2"><ellipse cx="35" cy="35" rx="30" ry="12"/><ellipse cx="35" cy="35" rx="30" ry="12" transform="rotate(60 35 35)"/><ellipse cx="35" cy="35" rx="30" ry="12" transform="rotate(-60 35 35)"/><circle cx="35" cy="35" r="11" fill="#0b2a8a"/><text x="35" y="40" fill="#fff" stroke="none" font-size="13" text-anchor="middle" font-family="Poppins,sans-serif">AI</text></svg><span>Generative AI</span></div>
  <div class="tile" style="left:471px;top:201px"><svg width="70" height="70" viewBox="0 0 70 70" fill="none" stroke="#1d1f2e" stroke-width="2"><circle cx="35" cy="35" r="22"/><circle cx="35" cy="35" r="13"/><circle cx="35" cy="35" r="4"/><path d="M4 14V4h10M56 4h10v10M66 56v10H56M14 66H4V56"/></svg><span>Capture Management</span></div>
  <div class="tile" style="left:762px;top:201px"><svg width="70" height="70" viewBox="0 0 70 70" fill="none" stroke="#1d1f2e" stroke-width="2"><rect x="8" y="6" width="48" height="58" rx="2"/><path d="M8 16h48M16 26h24M16 34h20M16 42h16M16 50h18M40 54l18-22 5 4-18 22-6 2z"/></svg><span>Technical Writer</span></div>
  <div class="tile" style="left:181px;top:405px"><svg width="70" height="70" viewBox="0 0 70 70" fill="none" stroke="#1d1f2e" stroke-width="2"><rect x="8" y="6" width="48" height="58" rx="2"/><path d="M8 16h48M16 24h14v12H16zM36 26h12M36 32h12M16 44h32M16 52h22M44 56l14-18 5 4-14 18-6 2z"/></svg><span>Book Boss</span></div>
  <div class="tile" style="left:471px;top:405px"><svg width="70" height="70" viewBox="0 0 70 70" fill="none" stroke="#1d1f2e" stroke-width="2"><rect x="10" y="6" width="44" height="58" rx="2"/><text x="30" y="26" fill="#1d1f2e" stroke="none" font-size="14" text-anchor="middle" font-family="Poppins,sans-serif">CV</text><path d="M18 34h26M18 42h22M18 50h18M42 58l18-26 4 3-18 26-6 2z"/></svg><span>Resume Writer</span></div>
  <div class="tile" style="left:762px;top:405px"><svg width="70" height="70" viewBox="0 0 70 70" fill="none" stroke="#1d1f2e" stroke-width="2"><rect x="4" y="10" width="62" height="40" rx="3"/><path d="M4 42h62M28 50l-3 10h20l-3-10M20 60h30"/></svg><span>Desktop Publishing</span></div>
  <a class="btn btn-dark" style="left:488px;top:619px;width:224px;height:56px">View Services <svg width="26" height="14" viewBox="0 0 26 14"><path d="M1 7h23M18 1l6 6-6 6" fill="none" stroke="currentColor" stroke-width="2"/></svg></a>
</section>

<section class="expertise"><h2>Subject Matter Expertise</h2></section>
<div class="arrow-btn" style="left:968px"><svg width="36" height="36" viewBox="0 0 36 36"><path d="M21 11l-7 7 7 7" fill="none" stroke="#fff" stroke-width="2"/></svg></div>
<div class="arrow-btn" style="left:1047px"><svg width="36" height="36" viewBox="0 0 36 36"><path d="M15 11l7 7-7 7" fill="none" stroke="#fff" stroke-width="2"/></svg></div>
<div class="ex-card" style="left:108px"><div class="photo" role="img" aria-label="Glowing circuit board with a brain shape" style="background:radial-gradient(circle at 50% 45%,#4fb8ff,#0a3a8a 55%,#061a4a)"></div><span>Generative AI</span></div>
<div class="ex-card" style="left:440px"><div class="photo" role="img" aria-label="Engineer viewing data screens" style="background:linear-gradient(90deg,#1a2a2e,#2c5a5e 60%,#4f8a88)"></div><span>Systems Engineering</span></div>
<div class="ex-card" style="left:770px"><div class="photo" role="img" aria-label="Overhead view of a warehouse with stacked boxes" style="background:linear-gradient(135deg,#8a6a44,#c9a878 50%,#5a5046)"></div><span>Logistics</span></div>

<section class="contact">
  <h2 class="section-title" style="top:56px">Contact Us</h2>
  <div class="field" style="left:164px;top:149px;width:426px">Full Name</div>
  <div class="field" style="left:608px;top:149px;width:428px">Last Name</div>
  <div class="field" style="left:164px;top:228px;width:426px">Email Address</div>
  <div class="field" style="left:608px;top:228px;width:428px">Phone Number</div>
  <div class="field" style="left:164px;top:311px;width:872px;height:123px">Message...</div>
  <a class="btn btn-dark" style="left:488px;top:471px;width:224px;height:56px">Submit Now <svg width="26" height="14" viewBox="0 0 26 14"><path d="M1 7h23M18 1l6 6-6 6" fill="none" stroke="currentColor" stroke-width="2"/></svg></a>
</section>

<h2 class="section-title" style="top:4431px">Testimonials</h2>
<div class="quote-card faded" style="left:-263px"><p>"Sed ut perspiciatis unde omnis iste natus error sit voluptatem accusantium doloremque laudantium, totam rem aperiam, eaque ipsa quae ab illo inventore veritatis et quasi architecto beatae vitae dicta sunt explicabo"</p><cite>- Lorem Lipsum</cite></div>
<div class="quote-card" style="left:318px"><span class="qmark" style="left:40px">”</span><p>"Sed ut perspiciatis unde omnis iste natus error sit voluptatem accusantium doloremque laudantium, totam rem aperiam, eaque ipsa quae ab illo inventore veritatis et quasi architecto beatae vitae dicta sunt explicabo"</p><cite>- Lorem Lipsum</cite></div>
<div class="quote-card faded" style="left:899px"><span class="qmark" style="left:40px">”</span><p>"Sed ut perspiciatis unde omnis iste natus error sit voluptatem accusantium doloremque laudantium, totam rem aperiam, eaque ipsa quae ab illo inventore veritatis et quasi architecto beatae vitae dicta sunt explicabo"</p><cite>- Lorem Lipsum</cite></div>
<div class="dot" style="left:533px;background:var(--navy)"></div>
<div class="dot" style="left:583px"></div>
<div class="dot" style="left:633px"></div>

<footer class="site-footer">
  <div class="abs serif" style="left:150px;top:150px;font-size:32px;line-height:1">The Quill Draft<span style="display:block;font-size:14px;padding-left:40px;margin-top:2px">Consulting LLC</span></div>
  <h4 style="left:519px">Quick links</h4>
  <nav class="flinks"><a>Home</a><a>Work with Us</a><a>Work for Us</a><a>About Us</a><a>Contact</a></nav>
  <h4 style="left:791px">Contact Details</h4>
  <svg class="abs" style="left:793px;top:121px" width="16" height="16" viewBox="0 0 24 24"><path fill="#fff" d="M6.6 10.8a15 15 0 006.6 6.6l2.2-2.2a1 1 0 011-.25 11.4 11.4 0 003.6.6 1 1 0 011 1V20a1 1 0 01-1 1A17 17 0 013 4a1 1 0 011-1h3.5a1 1 0 011 1c0 1.25.2 2.45.57 3.57a1 1 0 01-.25 1z"/></svg>
  <div class="fcontact" style="top:119px">(410) 555-0147</div>
  <svg class="abs" style="left:793px;top:162px" width="17" height="13" viewBox="0 0 17 13"><rect x="0.5" y="0.5" width="16" height="12" fill="#fff"/><path d="M1 1l7.5 6L16 1" fill="none" stroke="#070a3a" stroke-width="1.4"/></svg>
  <div class="fcontact" style="top:159px">info@quilldraft.com</div>
  <div class="abs" style="left:457px;top:350px;width:581px;height:1px;background:rgba(255,255,255,.35)"></div>
  <div class="copyright">@Copyrights 2023. All Rights Reserved.</div>
</footer>

</body>
</html>
```